Wedding Planning and Event Planners website

I am driven by perfection of my occupation and i look forward to having an attractive and contemporary website for an event and wedding planning group. We are located in the United States and Canada and we offer our services only in these two countries. My website is for people who are planning events such Church programs, weddings, musical concerts, Picnic, etc. My website should have imaginary of events such as weddings, musical concerts and picnic, etc.. I don't have any reference website because i want all designers to be creative and unique. I prefer blue,red,green,yellow colors.

Industry/Entity Type

Wedding

Coding

Coded - Design and coding required

```html
<!DOCTYPE html>
<html lang="en">
<head>
<meta charset="utf-8">
<title>Rosalind Planners — Wedding &amp; Event Planning</title>
<link rel="stylesheet" href="https://fonts.googleapis.com/css2?family=Open+Sans:wght@400;600;700;800&display=swap">
<style>
:root{
  --blue:#1769c2;
  --blue-dark:#0f56a6;
  --red:#e31e24;
  --red-dark:#b8060c;
  --yellow:#ffe500;
  --ink:#333;
  --muted:#666;
  --grey-bg:#eeeeee;
  --white:#fff;
}
*{box-sizing:border-box;margin:0;padding:0}
html,body{width:1200px;height:4433px;overflow:hidden}
body{font-family:"Open Sans",Arial,sans-serif;color:var(--ink);background:var(--white)}
section,header,nav,footer{position:relative;width:1200px;overflow:hidden}
.abs{position:absolute}
a{color:inherit;text-decoration:none}

/* header */
.site-header{height:98px;background:var(--white)}
.brand{left:77px;top:14px;font-weight:700;color:var(--blue);font-size:30px;line-height:34px}
.top-contact{right:77px;top:32px;font-size:15px;color:var(--red);display:flex;gap:14px;align-items:center}
.top-contact span{display:flex;align-items:center;gap:7px}
.top-contact .sep{color:#999}

/* nav */
.main-nav{height:56px;background:linear-gradient(var(--blue),var(--blue-dark))}
.main-nav ul{list-style:none;display:flex;justify-content:space-between;padding:0 56px;height:56px;align-items:center}
.main-nav li{color:var(--white);font-size:14px;font-weight:700;text-transform:uppercase}

/* hero */
.hero{height:514px;background:linear-gradient(100deg,#2a2420 0%,#5a4636 40%,#8a7565 65%,#3a3e48 100%)}
.hero-title{left:77px;top:132px;color:var(--white);font-size:40px;font-weight:800;line-height:46px;text-transform:uppercase}
.hero-sub{left:77px;top:226px;color:var(--yellow);font-size:28px;font-weight:800;text-transform:uppercase}
.btn{display:inline-block;font-size:13px;font-weight:700;text-transform:uppercase;text-align:center}
.btn-red{background:var(--red);color:var(--white)}
.btn-yellow{background:var(--yellow);color:var(--red)}
.hero .btn{left:77px;top:290px;width:145px;height:40px;line-height:40px}
.dots{left:77px;top:596px;display:flex;gap:8px}
.dots i{width:12px;height:12px;border-radius:50%;background:var(--white)}
.dots i:first-child{background:var(--yellow)}
.dots{top:442px}

/* section titles */
.section-title{left:0;width:1200px;text-align:center;font-size:28px;font-weight:700;text-transform:uppercase;color:var(--blue)}
.divider{left:0;width:1200px;display:flex;justify-content:center}
.on-dark{color:var(--white)}

/* welcome */
.welcome{height:337px}
.welcome .section-title{top:34px}
.welcome .divider{top:80px}
.welcome p{left:106px;width:988px;top:110px;text-align:center;font-size:15px;line-height:21px;color:var(--muted)}
.welcome .btn{left:523px;top:248px;width:154px;height:44px;line-height:44px}

/* what we do */
.what-we-do{height:970px;background:var(--grey-bg)}
.what-we-do .section-title{top:34px}
.what-we-do .divider{top:80px}
.photo{border:6px solid var(--white);box-shadow:0 0 4px rgba(0,0,0,.25)}
.photo-wedding{left:77px;top:145px;width:523px;height:384px;background:linear-gradient(160deg,#d9dfe3,#8aa070 55%,#5c6f3e)}
.photo-event{left:603px;top:529px;width:520px;height:381px;background:linear-gradient(160deg,#f2ece4,#b58455 50%,#3b2a1f)}
.service-card{width:626px;height:266px;background:var(--white);padding:28px 30px;box-shadow:0 0 6px rgba(0,0,0,.12)}
.card-wedding{left:497px;top:177px}
.card-event{left:77px;top:562px}
.service-card h3{color:var(--red);font-size:22px;font-weight:700;text-transform:uppercase;margin-bottom:12px}
.service-card p{font-size:15px;line-height:22px;color:var(--muted)}
.service-card .btn{position:absolute;width:148px;height:40px;line-height:40px;bottom:22px}
.card-wedding .btn{left:200px}
.card-event .btn{left:13px}

/* offers */
.offers{height:464px;background:linear-gradient(120deg,var(--red-dark),var(--red) 45%,#c40a10)}
.offers .section-title{top:52px}
.offers .divider{top:98px}
.offer{top:165px;width:250px;text-align:center;color:var(--white)}
.offer .icon{width:94px;height:94px;border-radius:50%;background:var(--yellow);margin:0 auto;display:flex;align-items:center;justify-content:center}
.offer h4{margin-top:20px;font-size:17px;font-weight:700;text-transform:uppercase;color:var(--yellow)}
.offer p{margin-top:8px;font-size:15px;line-height:21px}

/* news */
.news{height:570px}
.news .section-title{top:44px}
.news .divider{top:90px}
.news-item{top:133px;width:328px}
.news-img{height:186px}
.news-item .date{margin-top:16px;color:var(--red);font-size:16px;font-weight:700}
.news-item p{margin-top:6px;font-size:15px;line-height:20px;color:var(--muted)}
.news-item p b{color:var(--blue);font-size:12px}
.news .btn{left:484px;top:493px;width:232px;height:40px;line-height:40px}

/* gallery */
.gallery{height:523px;background:var(--blue)}
.gallery .section-title{top:48px}
.gallery .divider{top:94px}
.gallery-grid{left:0;top:145px;width:1200px;height:311px;display:grid;grid-template-columns:repeat(4,1fr);grid-template-rows:repeat(2,1fr);gap:2px}
.gallery-grid div{}
.arrow{top:282px;width:38px;height:38px;border-radius:50%;background:var(--yellow);display:flex;align-items:center;justify-content:center}

/* testimonials */
.testimonials{height:533px}
.testimonials .section-title{top:40px}
.testimonials .divider{top:86px}
.quote{top:128px;text-align:center}
.quote p{font-size:14px;line-height:20px;font-style:italic;color:var(--muted);padding:0 40px}
.quote .mark{position:absolute;font-size:90px;font-weight:800;color:#dedede;line-height:1}
.quote .open{left:0;top:-20px}
.quote .close{right:0;top:80px}
.avatar{width:82px;height:82px;border-radius:50%;margin:40px auto 0;border:3px solid var(--white);box-shadow:0 0 4px rgba(0,0,0,.3);background:linear-gradient(#9ab0c4,#5c6f80)}
.quote h5{margin-top:32px;color:var(--red);font-size:13px;font-weight:700;text-transform:uppercase}
.testimonials .btn{left:484px;top:453px;width:232px;height:40px;line-height:40px}

/* footer */
.site-footer{height:304px;background:var(--blue);color:var(--white)}
.site-footer h6{font-size:15px;font-weight:700;text-transform:uppercase;color:var(--yellow);margin-bottom:10px}
.footer-col{top:52px;font-size:13px;line-height:22px}
.footer-col ul{list-style:none}
.two-col{display:flex;gap:48px}
.contact-line{display:flex;align-items:center;gap:8px}
.news-input{width:242px;height:38px;background:var(--white);color:#999;font-size:13px;padding:0 10px;line-height:38px}
.news-btn{margin-top:14px;width:82px;height:36px;line-height:36px}
.footer-brand{left:881px;top:210px;font-size:40px;font-weight:700;line-height:44px;color:#4f93dc}
.bottom-bar{height:64px;background:var(--blue-dark);color:var(--white)}
.copyright{left:77px;top:22px;font-size:12px}
.social{right:77px;top:16px;display:flex;gap:10px}
.social i{width:30px;height:30px;border-radius:50%;border:2px solid var(--white)}
</style>
</head>
<body>

<header class="site-header">
  <div class="abs brand">Rosalind<br>Planners</div>
  <div class="abs top-contact">
    <span><svg width="14" height="14" viewBox="0 0 24 24"><path fill="#e31e24" d="M6.6 10.8c1.4 2.8 3.8 5.1 6.6 6.6l2.2-2.2c.3-.3.7-.4 1-.2 1.1.4 2.3.6 3.6.6.6 0 1 .4 1 1V20c0 .6-.4 1-1 1C10.6 21 3 13.4 3 4c0-.6.4-1 1-1h3.5c.6 0 1 .4 1 1 0 1.3.2 2.5.6 3.6.1.3 0 .7-.2 1z"/></svg>1-800-555-0142</span>
    <span class="sep">|</span>
    <span><svg width="14" height="12" viewBox="0 0 24 20"><rect x="1" y="1" width="22" height="18" fill="#e31e24"/><path d="M1 2l11 9 11-9" fill="none" stroke="#fff" stroke-width="2"/></svg>hello@rosalindplanners.example</span>
  </div>
</header>

<nav class="main-nav">
  <ul>
    <li>Home</li><li>About Us</li><li>Services</li><li>News &amp; Events</li><li>Blog</li><li>Testimonials</li><li>Careers</li><li>Gallery</li><li>Contact Us</li>
  </ul>
</nav>

<section class="hero" role="img" aria-label="Event planner holding a tablet at a banquet venue">
  <h1 class="abs hero-title">We are a wedding planning<br>and event planning</h1>
  <div class="abs hero-sub">We serve in the US &amp; Canada only</div>
  <a class="abs btn btn-red">Read More</a>
  <div class="abs dots"><i></i><i></i><i></i><i></i></div>
</section>

<section class="welcome">
  <h2 class="abs section-title">Welcome to Rosalind Planners</h2>
  <div class="abs divider"><svg width="110" height="14"><line x1="0" y1="7" x2="46" y2="7" stroke="#bbb"/><circle cx="55" cy="7" r="5" fill="none" stroke="#bbb"/><line x1="64" y1="7" x2="110" y2="7" stroke="#bbb"/></svg></div>
  <p class="abs">Aliquam molestie, mi et imperdiet euismod, dui purus auctor tellus, et interdum lacus lectus et ante. Sed accumsan sollicitudin sapien, sit amet adipiscing turpis gravida ac. In congue, neque ac lobortis volutpat, libero mauris varius mi, vitae suscipit ipsum ligula vitae risus. Duis aliquam nibh a dui iaculis viverra id a velit. Vivamus egestas risus in magna varius commodo. Sed semper viverra egestas. Etiam pretium porttitor lectus, vel ornare neque porta volutpat.</p>
  <a class="abs btn btn-yellow">Read More</a>
</section>

<section class="what-we-do">
  <h2 class="abs section-title">What We Do</h2>
  <div class="abs divider"><svg width="110" height="14"><line x1="0" y1="7" x2="46" y2="7" stroke="#bbb"/><circle cx="55" cy="7" r="5" fill="none" stroke="#bbb"/><line x1="64" y1="7" x2="110" y2="7" stroke="#bbb"/></svg></div>
  <div class="abs photo photo-wedding" role="img" aria-label="Newlywed couple walking through cheering guests outdoors"></div>
  <div class="abs photo photo-event" role="img" aria-label="Wine glasses and canapés on a catering table"></div>
  <article class="abs service-card card-wedding">
    <h3>Wedding Planning</h3>
    <p>Aliquam molestie, mi et imperdiet euismod, dui purus auctor tellus, et interdum lacus lectus et ante. Sed accumsan sollicitudin sapien, sit amet adipiscing turpis gravida ac. In congue, neque ac lobortis volutpat, libero mauris varius mi, vitae suscipit ipsum ligula vitae risus. Duis aliquam nibh a dui iaculis viverra id a velit.</p>
    <a class="btn btn-yellow">Read More</a>
  </article>
  <article class="abs service-card card-event">
    <h3>Event Planning</h3>
    <p>Aliquam molestie, mi et imperdiet euismod, dui purus auctor tellus, et interdum lacus lectus et ante. Sed accumsan sollicitudin sapien, sit amet adipiscing turpis gravida ac. In congue, neque ac lobortis volutpat, libero mauris varius mi, vitae suscipit ipsum ligula vitae risus. Duis aliquam nibh a dui iaculis viverra id a velit.</p>
    <a class="btn btn-yellow">Read More</a>
  </article>
</section>

<section class="offers">
  <h2 class="abs section-title on-dark">Our Service Offers</h2>
  <div class="abs divider"><svg width="110" height="14"><line x1="0" y1="7" x2="46" y2="7" stroke="#fff"/><circle cx="55" cy="7" r="5" fill="none" stroke="#fff"/><line x1="64" y1="7" x2="110" y2="7" stroke="#fff"/></svg></div>
  <div class="abs offer" style="left:70px">
    <div class="icon"><svg width="44" height="44" viewBox="0 0 44 44"><path fill="#c40a10" d="M22 4v6M19 7h6" stroke="#c40a10" stroke-width="2"/><path fill="#c40a10" d="M22 12l12 10v18H10V22z"/><rect x="19" y="30" width="6" height="10" fill="#ffe500"/></svg></div>
    <h4>Church Programs</h4>
    <p>Aliquam molestie, mi et imperdiet euismod, dui purus auctor tellus, et interdum lacus lectus et ante.</p>
  </div>
  <div class="abs offer" style="left:342px">
    <div class="icon"><svg width="44" height="44" viewBox="0 0 44 44"><circle cx="17" cy="25" r="9" fill="none" stroke="#c40a10" stroke-width="4"/><circle cx="27" cy="21" r="9" fill="none" stroke="#c40a10" stroke-width="4"/></svg></div>
    <h4>Weddings</h4>
    <p>Aliquam molestie, mi et imperdiet euismod, dui purus auctor tellus, et interdum lacus lectus et ante.</p>
  </div>
  <div class="abs offer" style="left:611px">
    <div class="icon"><svg width="44" height="44" viewBox="0 0 44 44"><path d="M18 32V10l16-4v22" fill="none" stroke="#c40a10" stroke-width="4"/><circle cx="13" cy="32" r="6" fill="#c40a10"/><circle cx="29" cy="28" r="6" fill="#c40a10"/></svg></div>
    <h4>Musical Concerts</h4>
    <p>Aliquam molestie, mi et imperdiet euismod, dui purus auctor tellus, et interdum lacus lectus et ante.</p>
  </div>
  <div class="abs offer" style="left:880px">
    <div class="icon"><svg width="44" height="44" viewBox="0 0 44 44"><path d="M12 18a10 10 0 0 1 20 0" fill="none" stroke="#c40a10" stroke-width="3"/><path fill="#c40a10" d="M6 18h32l-4 20H10z"/></svg></div>
    <h4>Picnic</h4>
    <p>Aliquam molestie, mi et imperdiet euismod, dui purus auctor tellus, et interdum lacus lectus et ante.</p>
  </div>
</section>

<section class="news">
  <h2 class="abs section-title">Latest News &amp; Events</h2>
  <div class="abs divider"><svg width="110" height="14"><line x1="0" y1="7" x2="46" y2="7" stroke="#bbb"/><circle cx="55" cy="7" r="5" fill="none" stroke="#bbb"/><line x1="64" y1="7" x2="110" y2="7" stroke="#bbb"/></svg></div>
  <article class="abs news-item" style="left:77px">
    <div class="news-img" role="img" aria-label="Wedding reception dance under evening lights" style="background:linear-gradient(150deg,#2d3a2a,#6f7b52 50%,#1d1d18)"></div>
    <div class="date">AUG 04, 2016</div>
    <p>Aliquam molestie, mi et imperdiet euismod, dui purus auctor tellus, et interdum lacus lectus et ante...<b>Read More</b></p>
  </article>
  <article class="abs news-item" style="left:435px">
    <div class="news-img" role="img" aria-label="Concert crowd in front of a lit stage" style="background:linear-gradient(160deg,#2b2f6b,#7a4aa0 45%,#c89060 70%,#1a1630)"></div>
    <div class="date">AUG 04, 2016</div>
    <p>Aliquam molestie, mi et imperdiet euismod, dui purus auctor tellus, et interdum lacus lectus et ante...<b>Read More</b></p>
  </article>
  <article class="abs news-item" style="left:792px">
    <div class="news-img" role="img" aria-label="Decorated banquet hall with pink table settings" style="background:linear-gradient(160deg,#f4e8ec,#e6b7c8 50%,#c98aa2)"></div>
    <div class="date">AUG 04, 2016</div>
    <p>Aliquam molestie, mi et imperdiet euismod, dui purus auctor tellus, et interdum lacus lectus et ante...<b>Read More</b></p>
  </article>
  <a class="abs btn btn-yellow">View All News &amp; Events</a>
</section>

<section class="gallery">
  <h2 class="abs section-title on-dark">Gallery</h2>
  <div class="abs divider"><svg width="110" height="14"><line x1="0" y1="7" x2="46" y2="7" stroke="#fff"/><circle cx="55" cy="7" r="5" fill="none" stroke="#fff"/><line x1="64" y1="7" x2="110" y2="7" stroke="#fff"/></svg></div>
  <div class="abs gallery-grid">
    <div role="img" aria-label="Banquet hall with chandeliers" style="background:linear-gradient(160deg,#4a2a1c,#b07a4a)"></div>
    <div role="img" aria-label="Outdoor wedding tables under a canopy" style="background:linear-gradient(160deg,#d8d0c0,#9a8a6c)"></div>
    <div role="img" aria-label="Wine glasses at a dinner event" style="background:linear-gradient(160deg,#c8c0b0,#4a3a2c)"></div>
    <div role="img" aria-label="Friends celebrating at a picnic" style="background:linear-gradient(160deg,#7ab0d8,#c89a6a)"></div>
    <div role="img" aria-label="Band performing on a concert stage" style="background:linear-gradient(160deg,#1a2250,#4a4ab0 60%,#c06a30)"></div>
    <div role="img" aria-label="Wedding reception tables outdoors" style="background:linear-gradient(160deg,#e0dcd4,#8a9478)"></div>
    <div role="img" aria-label="Fireworks above a castle at night" style="background:linear-gradient(160deg,#3a6ab8,#d8a050 60%,#6a3a20)"></div>
    <div role="img" aria-label="Garden party with balloons" style="background:linear-gradient(160deg,#6ab04a,#e0c040 60%,#3a7a2a)"></div>
  </div>
  <div class="abs arrow" style="left:8px"><svg width="14" height="14" viewBox="0 0 14 14"><path d="M9 2L4 7l5 5" fill="none" stroke="#1769c2" stroke-width="3"/></svg></div>
  <div class="abs arrow" style="right:8px"><svg width="14" height="14" viewBox="0 0 14 14"><path d="M5 2l5 5-5 5" fill="none" stroke="#1769c2" stroke-width="3"/></svg></div>
</section>

<section class="testimonials">
  <h2 class="abs section-title">Testimonials</h2>
  <div class="abs divider"><svg width="110" height="14"><line x1="0" y1="7" x2="46" y2="7" stroke="#bbb"/><circle cx="55" cy="7" r="5" fill="none" stroke="#bbb"/><line x1="64" y1="7" x2="110" y2="7" stroke="#bbb"/></svg></div>
  <div class="abs quote" style="left:100px;width:470px">
    <span class="mark open">&ldquo;</span><span class="mark close">&rdquo;</span>
    <p>Donec in est erat, id malesuada turpis. Nunc a dui id turpis convallis semper. Nunc dignissim lectus vitae eros placerat euismod. Aenean lacinia sodales eros, sit amet molestie enim consectetur eget. Nunc dignissim lectus vitae eros placerat euismod. Aenean lacinia sodales eros, sit amet molestie enim consectetur eget.</p>
    <div class="avatar" role="img" aria-label="Client portrait"></div>
    <h5>Name Heading</h5>
  </div>
  <div class="abs quote" style="left:630px;width:470px">
    <span class="mark open">&ldquo;</span><span class="mark close">&rdquo;</span>
    <p>Donec in est erat, id malesuada turpis. Nunc a dui id turpis convallis semper. Nunc dignissim lectus vitae eros placerat euismod. Aenean lacinia sodales eros, sit amet molestie enim consectetur eget. Nunc dignissim lectus vitae eros placerat euismod. Aenean lacinia sodales eros, sit amet molestie enim consectetur eget.</p>
    <div class="avatar" role="img" aria-label="Client portrait"></div>
    <h5>Name Heading</h5>
  </div>
  <a class="abs btn btn-yellow">Read All Testimonials</a>
</section>

<footer class="site-footer">
  <div class="abs footer-col" style="left:77px">
    <h6>Company</h6>
    <div class="two-col">
      <ul><li>Home</li><li>About Us</li><li>Services</li><li>News &amp; Events</li><li>Blog Posts</li><li>Testimonials</li><li>Careers</li></ul>
      <ul><li>Gallery</li><li>Contact Us</li></ul>
    </div>
  </div>
  <div class="abs footer-col" style="left:355px">
    <h6>Services</h6>
    <ul><li>Duis aliquam nibh</li><li>Dui iaculis viverra</li><li>Vivamus egestas</li><li>Risus in magna varius</li><li>Commodo</li><li>Sed semper viverra</li></ul>
  </div>
  <div class="abs footer-col" style="left:615px;width:230px">
    <h6>Contact Info</h6>
    <div style="font-weight:700">ROSALIND PLANNERS</div>
    <div>1420 Linden Avenue,<br>Portland, OR 97205</div>
    <div class="contact-line"><svg width="12" height="12" viewBox="0 0 24 24"><path fill="#ffe500" d="M6.6 10.8c1.4 2.8 3.8 5.1 6.6 6.6l2.2-2.2c.3-.3.7-.4 1-.2 1.1.4 2.3.6 3.6.6.6 0 1 .4 1 1V20c0 .6-.4 1-1 1C10.6 21 3 13.4 3 4c0-.6.4-1 1-1h3.5c.6 0 1 .4 1 1 0 1.3.2 2.5.6 3.6.1.3 0 .7-.2 1z"/></svg>1-800-555-0142</div>
    <div class="contact-line"><svg width="12" height="10" viewBox="0 0 24 20"><rect x="1" y="1" width="22" height="18" fill="#ffe500"/><path d="M1 2l11 9 11-9" fill="none" stroke="#1769c2" stroke-width="2"/></svg>hello@rosalindplanners.example</div>
    <div class="contact-line"><svg width="10" height="14" viewBox="0 0 20 28"><path fill="#ffe500" d="M10 0a10 10 0 0 0-10 10c0 7 10 18 10 18s10-11 10-18A10 10 0 0 0 10 0z"/><circle cx="10" cy="10" r="4" fill="#1769c2"/></svg>Map Location</div>
  </div>
  <div class="abs footer-col" style="left:881px">
    <h6>Newsletter Sign Up</h6>
    <div class="news-input">Enter Email Address</div>
    <a class="btn btn-yellow news-btn" style="float:right">Sign Up</a>
  </div>
  <div class="abs footer-brand">Rosalind<br>Planners</div>
</footer>

<div class="bottom-bar" style="position:relative">
  <div class="abs copyright">Copyright © 2016. Company Name. All Right Reserved</div>
  <div class="abs social"><i></i><i></i><i></i><i></i><i></i><i></i></div>
</div>

</body>
</html>
```